Dietitian needs awesome business card

I need a contemporary design that's eye catching but professional.
My card is to given to doctors, specialists and patients alike.
I manage patients with chronic diseases
I have uploaded my logo and current business card, I would also like the other Certified Clinical Nutritionist logo incorporated into the design

Target Market(s)

Doctors, specialists and patients

Industry/Entity Type

Healthcare

Contact Information for Business Card

www.brightfieldnutrition.com.au
Ph: 0427 561 903
Fax: 6457 2183
email: marcus.k.diet@fernmail.com
Space on the back of the card with: Appointment date, Appointment time and appointment location

Font styles to use
Serif

Colors
fbee3e
876aae
ffc214

Requirements
Must have
• My Logo
• Certified Clinical Nutritionist Logo
• My 4 locations - Pinebrook Medical Centre, North Corrin Health, Hollis Medical, Ashcombe Doctors Surgery
Nice to have
• I like the colours in my current business card

```html
<!DOCTYPE html>
<html lang="en">
<head>
<meta charset="utf-8">
<title>Brightfield Nutrition &amp; Dietetics – Business Card</title>
<link rel="stylesheet" href="https://fonts.googleapis.com/css2?family=Open+Sans:wght@400;600&display=swap">
<style>
  :root {
    --page-bg: #2b2b2b;
    --card-white: #ffffff;
    --card-mint: #e4f2d2;
    --brand-blue: #23399a;
    --brand-green: #7dbb2a;
    --text-grey: #4a4a4a;
    --rule-blue: #9aa6d6;
    --badge-orange: #f26b21;
    --soft-circle-a: #d8def2;
    --soft-circle-b: #eef4e4;
  }
  * { box-sizing: border-box; margin: 0; padding: 0; }
  html, body { width: 1200px; height: 987px; overflow: hidden; }
  body {
    background: var(--page-bg);
    font-family: "Open Sans", Arial, sans-serif;
    position: relative;
  }
  .card {
    position: absolute;
    left: 293px;
    width: 615px;
    height: 352px;
    overflow: hidden;
  }
  .card--front { top: 130px; background: var(--card-white); }
  .card--back { top: 505px; background: var(--card-mint); }

  .brand {
    position: absolute;
    display: flex;
    align-items: center;
    gap: 12px;
  }
  .brand__dot {
    width: 58px; height: 58px;
    border-radius: 50%;
    background: var(--brand-green);
    flex: none;
  }
  .brand__name {
    color: var(--brand-blue);
    font-weight: 400;
    font-size: 23px;
    line-height: 1.15;
  }
  .card--front .brand { left: 32px; top: 26px; }
  .card--back .brand { left: 50%; top: 42px; transform: translateX(-50%); }
  .card--back .brand__dot { width: 74px; height: 74px; }
  .card--back .brand__name { font-size: 29px; }

  .front__decor {
    position: absolute;
    right: -40px; top: 20px;
    width: 300px; height: 300px;
    border-radius: 50%;
    background: radial-gradient(circle at 35% 40%, var(--soft-circle-a), var(--soft-circle-b) 70%);
    opacity: 0.7;
  }

  .person { position: absolute; left: 120px; top: 130px; }
  .person__name { color: var(--brand-blue); font-weight: 600; font-size: 22px; }
  .person__role { color: var(--brand-green); font-size: 16px; margin-top: 2px; }
  .person__badge {
    width: 74px; height: 34px;
    background: var(--badge-orange);
    margin-top: 10px;
  }

  .contact {
    position: absolute; left: 120px; top: 248px;
    list-style: none;
    color: var(--text-grey);
    font-size: 16px;
  }
  .contact li { display: flex; align-items: center; gap: 8px; height: 24px; }
  .contact svg { width: 16px; height: 16px; fill: var(--brand-blue); flex: none; }

  .appointment {
    position: absolute; left: 40px; right: 40px; top: 208px;
    color: var(--brand-blue);
    font-size: 16px;
  }
  .appointment__row { display: flex; align-items: flex-end; gap: 6px; margin-bottom: 28px; }
  .appointment__rule { border-bottom: 1px solid var(--rule-blue); height: 18px; }
  .appointment__date { width: 250px; margin-right: 10px; }
  .appointment__time { width: 118px; }
  .appointment__location { flex: 1; }
  .appointment__ampm { font-size: 13px; }
  .website {
    position: absolute; left: 0; right: 0; top: 300px;
    text-align: center;
    color: var(--brand-blue);
    font-style: italic;
    font-size: 16px;
    letter-spacing: 2.5px;
  }
</style>
</head>
<body>
  <section class="card card--front">
    <div class="front__decor" role="img" aria-label="Faint brand decoration"></div>
    <div class="brand">
      <span class="brand__dot"></span>
      <span class="brand__name">Brightfield<br>Nutrition &amp; Dietetics</span>
    </div>
    <div class="person">
      <p class="person__name">Marcus Kellaway</p>
      <p class="person__role">Nutritionist &amp; Chef</p>
      <div class="person__badge" role="img" aria-label="Certified Clinical Nutritionist badge"></div>
    </div>
    <ul class="contact">
      <li><svg viewBox="0 0 16 16"><path d="M3 1l3 3-1.5 2a9 9 0 0 0 5.5 5.5L12 10l3 3-2 2C7 15 1 9 1 3z"/></svg>0427 561 903</li>
      <li><svg viewBox="0 0 16 16"><path d="M4 1h8v4H4zM1 6h14v7h-3v2H4v-2H1zm4 5v3h6v-3z"/></svg>6457 2183</li>
      <li><svg viewBox="0 0 16 16"><path d="M1 3h14v10H1zm1 1v1l6 4 6-4V4z"/></svg>marcus.k.diet@fernmail.com</li>
    </ul>
  </section>

  <section class="card card--back">
    <div class="brand">
      <span class="brand__dot"></span>
      <span class="brand__name">Brightfield<br>Nutrition &amp; Dietetics</span>
    </div>
    <div class="appointment">
      <div class="appointment__row">
        <span>Date :</span><span class="appointment__rule appointment__date"></span>
        <span>Time :</span><span class="appointment__rule appointment__time"></span>
        <span class="appointment__ampm">AM/PM</span>
      </div>
      <div class="appointment__row">
        <span>Location :</span><span class="appointment__rule appointment__location"></span>
      </div>
    </div>
    <p class="website">www.brightfieldnutrition.com.au</p>
  </section>
</body>
</html>
```